Recruitment of Trellan Staffing for the UK market

I want a website for the UK market to attract businesses and companies to come to us for Philipine labour. We want an information site that gives all information on what we do and how we can recruit Philippine labour.
This is a recruitment site for companies to contact us with their requirements for skilled workers coming from the Philipines over to the UK to work.

Target Market(s)

Uk Companies and businesses who want Philipine skilled workers

Industry/Entity Type

REcruitment

Coding

Number of Pages Required

5+ page

Font styles to use
Sans Serif

Colors
0054AA
0677BA
7BADD7
CADEEF
E8F1F8
0094D4
00A9DD
6FCCEA
C7EBF8
E9F6FB
EE7325
F08F49
F5BC92
FAE3D3
FDF4ED
EB3D1F
EC4F4E
F09395
F8D3D4
FCEDEE

Requirements
Must have
• Look professional and corperate with drop down menus for Home ,about, services,articles. training , contact us
Nice to have
• Look at Velmora recruitment- https://velmorarecruitment.example.co.uk/. This is my current site - https://www.trellanstaffing.example.com/
Should not have
• Cartoons or silly pictures , needs to be corperate looking

```html
<!DOCTYPE html>
<html lang="en">
<head>
<meta charset="utf-8">
<title>Trellan Staffing – Skilled Philippine Workers for UK Companies</title>
<link rel="stylesheet" href="https://fonts.googleapis.com/css2?family=Roboto+Condensed:wght@400;700&family=Lato:wght@400;700&family=Roboto:wght@400;500;700&display=swap">
<style>
:root{
  --red:#9f2a2c;
  --red-dark:#8a2224;
  --blue:#0d4fa8;
  --blue-deep:#0a3f8c;
  --ink:#1b1b1b;
  --text:#333;
  --muted:#6a6a6a;
  --line:#e2e2e2;
  --footer:#2a2a2a;
  --footer-bar:#1e1e1e;
  --white:#fff;
}
*{box-sizing:border-box;margin:0;padding:0}
html,body{width:1200px;height:3838px;overflow:hidden}
body{position:relative;background:var(--white);font-family:"Lato",sans-serif;color:var(--text)}
.abs{position:absolute}
.cond{font-family:"Roboto Condensed",sans-serif}

/* top bar */
.topbar{left:425px;top:0;width:775px;height:33px;background:var(--red);border-bottom-left-radius:30px;color:#fff;font:500 12px "Roboto",sans-serif;display:flex;align-items:center}
.topbar .item{display:flex;align-items:center;gap:7px}
.topbar .phone{margin-left:42px}
.topbar .mail{margin-left:84px}
.topbar .sep{margin-left:115px;width:1px;height:16px;background:#fff8}
.topbar .dots{margin-left:26px;display:flex;gap:11px}
.topbar .dots span{width:8px;height:8px;border-radius:50%;background:#fff}

/* header */
.logo{font:700 22px "Roboto Condensed",sans-serif;color:var(--red);letter-spacing:.3px}
.header-logo{left:112px;top:56px}
.nav{left:408px;top:64px;display:flex;gap:32px;font:700 14px "Roboto",sans-serif;color:var(--ink)}
.nav a{color:inherit;text-decoration:none}
.nav a.active{color:var(--red);border-bottom:1px solid var(--red)}
.search{left:884px;top:58px;width:207px;height:35px;border:1px solid #ddd;border-radius:18px;font:400 11px "Roboto",sans-serif;color:#888;padding:0 18px;display:flex;align-items:center;justify-content:space-between}

/* hero */
.hero{left:0;top:112px;width:1200px;height:671px;background:linear-gradient(100deg,#3b3a38 0%,#6b5a3e 35%,#4c4640 60%,#9b3b2c 85%,#c0503a 100%)}
.hero h1{left:109px;top:370px;width:600px;font:700 52px/65px "Roboto Condensed",sans-serif;color:#fff;text-shadow:0 2px 6px #0006}
.btn{display:inline-flex;align-items:center;gap:10px;background:var(--blue);color:#fff;font:700 15px "Roboto",sans-serif;text-transform:uppercase;border-radius:3px;justify-content:center}
.hero .btn{left:109px;top:590px;width:192px;height:58px;font-size:17px}
.contact-box{left:777px;top:112px;width:311px;height:421px;background:var(--blue)}
.contact-box h2{position:absolute;left:0;right:0;top:26px;text-align:center;font:700 25px "Roboto Condensed",sans-serif;color:#fff}
.field{position:absolute;left:14px;width:282px;height:44px;background:#fff;font:400 12px "Roboto",sans-serif;color:#777;padding:14px 12px}
.send{left:791px;top:506px;width:283px;height:50px;background:var(--red);color:#fff;font:700 15px "Roboto",sans-serif;display:flex;align-items:center;justify-content:center}

/* sections */
.photo{border-radius:0}
.title{font:700 38px/44px "Roboto Condensed",sans-serif;color:var(--ink)}
.title em{font-style:normal;color:var(--red)}
.rule{display:flex;gap:3px;align-items:center;height:5px}
.rule i{display:block;height:4px;background:var(--red);width:70px}
.rule b{display:block;height:4px;background:var(--blue);width:9px}
.para{font:400 15px/26px "Lato",sans-serif;color:var(--text);text-align:justify}
.section-btn{height:48px;width:167px;font-size:15px}

.circle-lg{left:131px;top:879px;width:358px;height:358px;border-radius:50%;border:5px solid var(--blue);background:linear-gradient(135deg,#7b6a4f,#c04a36 50%,#5d6b7a)}
.circle-sm{left:384px;top:1107px;width:156px;height:156px;border-radius:50%;border:4px solid #fff;box-shadow:0 4px 14px #0004;background:linear-gradient(135deg,#8ea6b9,#d9c8b8 50%,#5c7388)}

/* why choose */
.why{left:0;top:2245px;width:1200px;height:608px;background:linear-gradient(90deg,#a4302d,#b43b35 50%,#9f2a2c)}
.why h2{position:absolute;left:0;right:0;top:72px;text-align:center;font:700 40px "Roboto Condensed",sans-serif;color:#fff}
.why .rule{position:absolute;left:574px;top:131px}
.why .rule i{background:#fff;width:72px}
.why .rule b{background:#fff;width:10px}
.card{top:2435px;width:302px;height:336px;background:#fff;border-radius:14px;text-align:center}
.card .icon{position:absolute;left:103px;top:27px;width:96px;height:96px;border-radius:50%;background:var(--blue);border:4px solid #fff;box-shadow:0 0 0 2px var(--blue)}
.card h3{position:absolute;left:0;right:0;top:144px;font:700 17px "Roboto Condensed",sans-serif;color:var(--ink)}
.card p{position:absolute;left:16px;right:16px;top:173px;font:400 16px/26px "Lato",sans-serif;color:#666}
.card .more{position:absolute;left:0;right:0;top:292px;font:700 17px "Roboto Condensed",sans-serif;color:var(--blue);display:flex;justify-content:center;gap:10px;align-items:center}

.map{left:626px;top:2955px;width:417px;height:378px;border:4px solid #fff;box-shadow:0 2px 10px #0003;background:linear-gradient(160deg,#8fb2f2,#9ab9ef 60%,#a5c1ea)}
.arrow{width:40px;height:40px;border-radius:50%;background:#fff;box-shadow:0 1px 6px #0003;display:flex;align-items:center;justify-content:center}

/* footer */
.footer{left:0;top:3427px;width:1200px;height:351px;background:var(--footer);color:#ddd}
.foot-h{font:700 15px "Roboto Condensed",sans-serif;color:#fff;text-transform:uppercase}
.foot-h::after{content:"";display:block;width:60px;height:2px;background:#fff;margin-top:8px}
.links{font:400 13px/33px "Roboto",sans-serif;color:#ddd;list-style:none}
.cline{display:flex;align-items:center;gap:14px;font:400 12px/18px "Roboto",sans-serif;color:#ddd}
.cicon{width:26px;height:26px;border-radius:50%;background:#3a3a3a;display:flex;align-items:center;justify-content:center;flex:none}
.sub-text{font:400 11px/18px "Roboto",sans-serif;color:#ddd}
.sub-input{left:839px;top:3604px;width:204px;height:35px;background:#fff;border-radius:18px 0 0 18px;font:400 10px "Roboto",sans-serif;color:#888;padding:0 14px;display:flex;align-items:center}
.sub-btn{left:1043px;top:3604px;width:47px;height:35px;background:var(--blue);border-radius:0 18px 18px 0;display:flex;align-items:center;justify-content:center}
.soc{top:3662px;width:28px;height:28px;border-radius:50%;background:#fff}
.soc::after{content:"";position:absolute;left:10px;top:10px;width:8px;height:8px;border-radius:50%;background:var(--ink)}
.chat{left:1129px;top:3713px;width:40px;height:40px;border-radius:50%;background:var(--red);display:flex;align-items:center;justify-content:center}
.bottom{left:0;top:3778px;width:1200px;height:60px;background:var(--footer-bar);color:#ddd;font:400 13px "Roboto",sans-serif}
.bottom .copy{position:absolute;left:112px;top:22px}
.bottom .copy u{color:#fff;font-weight:500}
.bottom .legal{position:absolute;left:811px;top:22px;display:flex;gap:12px}
.bottom .code{position:absolute;left:1134px;top:24px;font-size:10px}
</style>
</head>
<body>

<div class="abs topbar">
  <span class="item phone"><svg width="11" height="11" viewBox="0 0 24 24"><path fill="#fff" d="M6.6 10.8a15 15 0 0 0 6.6 6.6l2.2-2.2c.3-.3.7-.4 1-.2 1.1.4 2.3.6 3.6.6.6 0 1 .4 1 1V20c0 .6-.4 1-1 1A17 17 0 0 1 3 4c0-.6.4-1 1-1h3.5c.6 0 1 .4 1 1 0 1.3.2 2.5.6 3.6.1.3 0 .7-.2 1z"/></svg>07700 900461</span>
  <span class="item mail"><svg width="12" height="10" viewBox="0 0 24 18"><path fill="#fff" d="M0 0h24v18H0zM2 2l10 7 10-7"/></svg>sales@trellanstaffing.example.com</span>
  <span class="sep"></span>
  <span class="dots"><span></span><span></span><span></span><span></span></span>
</div>

<div class="abs logo header-logo">Trellan Staffing</div>
<nav class="abs nav">
  <a class="active">Home</a><a>About</a><a>Services</a><a>Articles</a><a>Training</a><a>Contact us</a>
</nav>
<div class="abs search">Search<svg width="13" height="13" viewBox="0 0 24 24"><circle cx="10" cy="10" r="7" fill="none" stroke="#333" stroke-width="3"/><path d="M15 15l6 6" stroke="#333" stroke-width="3"/></svg></div>

<section class="abs hero" role="img" aria-label="Engineer in hard hat and safety vest reading plans on a factory floor"></section>
<h1 class="abs" style="left:109px;top:370px;width:620px;font:700 52px/65px 'Roboto Condensed',sans-serif;color:#fff;text-shadow:0 2px 6px #0006">Recruiting and placing Skilled Philippine workers into UK companies</h1>
<a class="abs btn" style="left:109px;top:590px;width:192px;height:58px;font-size:17px">Get Started <svg width="15" height="15" viewBox="0 0 20 20"><circle cx="10" cy="10" r="9" fill="#fff"/><path d="M8 6l4 4-4 4" stroke="#0d4fa8" stroke-width="2.4" fill="none"/></svg></a>

<form class="abs contact-box">
  <h2>CONTACT US TODAY</h2>
  <div class="field" style="top:78px">Name</div>
  <div class="field" style="top:130px">Email</div>
  <div class="field" style="top:181px">Phone</div>
  <div class="field" style="top:232px">Address</div>
  <div class="field" style="top:283px;height:89px">Message</div>
</form>
<div class="abs send">SEND YOUR MESSAGE</div>

<!-- What we do -->
<div class="abs circle-lg" role="img" aria-label="Worker in safety vest and hard hat inspecting machinery"></div>
<div class="abs circle-sm" role="img" aria-label="Two smiling professionals in office and work uniform"></div>
<h2 class="abs title" style="left:627px;top:916px">What We <em>Do</em></h2>
<div class="abs rule" style="left:627px;top:970px"><i></i><b></b><b></b></div>
<p class="abs para" style="left:627px;top:996px;width:444px">Our company has been estabilished in the Philippines for over 20 years. We have mainly been recruiting philippine workers for the off shore industry in asia but since brexit and the new rules on skilled workers entering the UK we have been working with UK companies who now have chance to recruit some of the finest hard working talent from the Philippines for their companies..</p>
<a class="abs btn section-btn" style="left:627px;top:1174px">Learn More <svg width="14" height="14" viewBox="0 0 20 20"><circle cx="10" cy="10" r="9" fill="#fff"/><path d="M8 6l4 4-4 4" stroke="#0d4fa8" stroke-width="2.4" fill="none"/></svg></a>

<!-- About -->
<h2 class="abs title" style="left:112px;top:1353px">What the business<br>is <em>About</em></h2>
<div class="abs rule" style="left:112px;top:1451px"><i></i><b></b><b></b></div>
<p class="abs para" style="left:112px;top:1478px;width:378px">We source skilled workers directly from the Philippines to work in the UK. With offices , training locations and specialist recruiters we can find the highest quality individuals to add value and resources to any UK buisness. We delivery quality based on vast experience over a number of years.</p>
<a class="abs btn section-btn" style="left:112px;top:1657px">Learn More <svg width="14" height="14" viewBox="0 0 20 20"><circle cx="10" cy="10" r="9" fill="#fff"/><path d="M8 6l4 4-4 4" stroke="#0d4fa8" stroke-width="2.4" fill="none"/></svg></a>
<div class="abs photo" style="left:532px;top:1353px;width:328px;height:359px;background:linear-gradient(160deg,#b9cde0,#eef2f5 50%,#8fb0cf)" role="img" aria-label="Doctor and nurse in a hospital setting"></div>
<div class="abs photo" style="left:872px;top:1353px;width:328px;height:359px;background:linear-gradient(160deg,#5d5a55,#c07a3c 40%,#6f6a62)" role="img" aria-label="Workers reviewing plans in a workshop with sparks behind"></div>

<!-- How we help -->
<div class="abs" style="left:118px;top:1806px;width:404px;height:352px;background:var(--blue)"></div>
<div class="abs photo" style="left:139px;top:1798px;width:402px;height:348px;background:linear-gradient(135deg,#c9a94a,#b9b39c 45%,#7f8f7e)" role="img" aria-label="Worker in yellow hard hat writing on a clipboard"></div>
<h2 class="abs title" style="left:638px;top:1823px">How We <em>Help</em></h2>
<div class="abs rule" style="left:640px;top:1877px"><i></i><b></b><b></b></div>
<p class="abs para" style="left:640px;top:1904px;width:442px">We work with companies to find skilled workers that meet the UK requirements for Visas and work permits. We guide you through the whole process and deliver highly trained people that add value to your business. We are here to help both the companies and the Philippino people to gain a better standard of living for their families.</p>
<a class="abs btn section-btn" style="left:640px;top:2082px">Learn More <svg width="14" height="14" viewBox="0 0 20 20"><circle cx="10" cy="10" r="9" fill="#fff"/><path d="M8 6l4 4-4 4" stroke="#0d4fa8" stroke-width="2.4" fill="none"/></svg></a>

<!-- Why choose -->
<section class="abs why">
  <h2>Why Choose Us</h2>
  <div class="rule"><i></i><b></b><b></b></div>
</section>
<article class="abs card" style="left:120px">
  <div class="icon"><svg width="88" height="88" viewBox="0 0 88 88"><rect x="30" y="24" width="28" height="38" rx="3" fill="none" stroke="#fff" stroke-width="3"/><path d="M36 34h16M36 42h16M36 50h10" stroke="#fff" stroke-width="3"/></svg></div>
  <h3>UK Skilled Workers List</h3>
  <p>The UK government since brexit have developed a new system based on points (similar to Australia) when recruiting from outside of the UK.</p>
  <div class="more">Read More <svg width="14" height="14" viewBox="0 0 20 20"><circle cx="10" cy="10" r="9" fill="#0d4fa8"/><path d="M8 6l4 4-4 4" stroke="#fff" stroke-width="2.4" fill="none"/></svg></div>
</article>
<article class="abs card" style="left:449px">
  <div class="icon"><svg width="88" height="88" viewBox="0 0 88 88"><rect x="30" y="24" width="28" height="38" rx="3" fill="none" stroke="#fff" stroke-width="3"/><circle cx="44" cy="40" r="6" fill="none" stroke="#fff" stroke-width="3"/><path d="M36 54h16" stroke="#fff" stroke-width="3"/></svg></div>
  <h3>Sponsor Licence</h3>
  <p>The UK government since brexit have developed a new system based on points (similar to Australia) when recruiting from outside of the UK.</p>
  <div class="more">Read More <svg width="14" height="14" viewBox="0 0 20 20"><circle cx="10" cy="10" r="9" fill="#0d4fa8"/><path d="M8 6l4 4-4 4" stroke="#fff" stroke-width="2.4" fill="none"/></svg></div>
</article>
<article class="abs card" style="left:778px">
  <div class="icon"><svg width="88" height="88" viewBox="0 0 88 88"><circle cx="42" cy="42" r="12" fill="none" stroke="#fff" stroke-width="3"/><path d="M51 51l10 10" stroke="#fff" stroke-width="4"/></svg></div>
  <h3>Recruitment Timeline</h3>
  <p>The UK government since brexit have developed a new system based on points (similar to Australia) when recruiting from outside of the UK.</p>
  <div class="more">Read More <svg width="14" height="14" viewBox="0 0 20 20"><circle cx="10" cy="10" r="9" fill="#0d4fa8"/><path d="M8 6l4 4-4 4" stroke="#fff" stroke-width="2.4" fill="none"/></svg></div>
</article>

<!-- Contact -->
<div class="abs arrow" style="left:63px;top:3123px"><svg width="12" height="12" viewBox="0 0 12 12"><path d="M8 2L4 6l4 4" stroke="#222" stroke-width="2" fill="none"/></svg></div>
<div class="abs arrow" style="left:1097px;top:3123px"><svg width="12" height="12" viewBox="0 0 12 12"><path d="M4 2l4 4-4 4" stroke="#222" stroke-width="2" fill="none"/></svg></div>
<h2 class="abs title" style="left:158px;top:2969px">Contact Us <em>Today</em></h2>
<div class="abs rule" style="left:158px;top:3024px"><i></i><b></b><b></b></div>
<p class="abs para" style="left:158px;top:3052px;width:373px">Please contact us today with your requirements , this can be care workers ,chef, welders, pipe fitters, caravan cabinet makers, medical workers. The UK list of required skills is extensive and the Philippines offerenglish speaking highly qualified hard working employees. Contact us today and make that first step to a highly motivated , quality skilled workforce.</p>
<a class="abs btn section-btn" style="left:158px;top:3263px">Learn More <svg width="14" height="14" viewBox="0 0 20 20"><circle cx="10" cy="10" r="9" fill="#fff"/><path d="M8 6l4 4-4 4" stroke="#0d4fa8" stroke-width="2.4" fill="none"/></svg></a>
<div class="abs map" role="img" aria-label="Map of the Philippine islands"></div>

<!-- Footer -->
<footer class="abs footer"></footer>
<div class="abs logo" style="left:112px;top:3594px">Trellan Staffing</div>
<div class="abs foot-h" style="left:407px;top:3495px">Quick Links</div>
<ul class="abs links" style="left:407px;top:3540px">
  <li>Home</li><li>About</li><li>Services</li><li>Articles</li><li>Training</li><li>Contact us</li>
</ul>
<div class="abs foot-h" style="left:568px;top:3495px">Contact Us</div>
<div class="abs cline" style="left:568px;top:3552px"><span class="cicon"><svg width="11" height="11" viewBox="0 0 24 24"><path fill="#fff" d="M6.6 10.8a15 15 0 0 0 6.6 6.6l2.2-2.2c.3-.3.7-.4 1-.2 1.1.4 2.3.6 3.6.6.6 0 1 .4 1 1V20c0 .6-.4 1-1 1A17 17 0 0 1 3 4c0-.6.4-1 1-1h3.5c.6 0 1 .4 1 1 0 1.3.2 2.5.6 3.6.1.3 0 .7-.2 1z"/></svg></span>07700 900461</div>
<div class="abs cline" style="left:568px;top:3597px"><span class="cicon"><svg width="11" height="9" viewBox="0 0 24 18"><path fill="#fff" d="M0 0h24v18H0z"/></svg></span>sales@trellanstaffing.example.com</div>
<div class="abs cline" style="left:568px;top:3648px"><span class="cicon"><svg width="10" height="13" viewBox="0 0 20 26"><path fill="#fff" d="M10 0a9 9 0 0 0-9 9c0 7 9 17 9 17s9-10 9-17a9 9 0 0 0-9-9zm0 12a3 3 0 1 1 0-6 3 3 0 0 1 0 6z"/></svg></span><span>Alder Close, Kelsby<br>KB4 7TR United Kingdom</span></div>
<div class="abs foot-h" style="left:831px;top:3495px">Subscribe to our blog</div>
<p class="abs sub-text" style="left:839px;top:3550px;width:240px">Sign up today to get resources on how to attract and retain more customers!</p>
<div class="abs sub-input">Email Address</div>
<div class="abs sub-btn"><svg width="16" height="16" viewBox="0 0 24 24"><path fill="#fff" d="M2 12l20-9-6 19-4-8z"/></svg></div>
<span class="abs soc" style="left:834px"></span>
<span class="abs soc" style="left:873px"></span>
<span class="abs soc" style="left:911px"></span>
<span class="abs soc" style="left:951px"></span>
<div class="abs chat"><svg width="18" height="16" viewBox="0 0 24 20"><path fill="#fff" d="M12 0C5 0 0 4 0 9c0 3 2 5 4 6l-1 5 5-3c1 0 3 1 4 1 7 0 12-4 12-9S19 0 12 0z"/></svg></div>
<div class="abs bottom">
  <span class="copy">Copyright© 2023 &nbsp;<u>Trellan Staffing Ltd</u> &nbsp;| &nbsp;All Rights Reserved</span>
  <span class="legal"><span>Specifications</span>|<span>Site Map</span>|<span>Privacy Policy</span></span>
  <span class="code">C47</span>
</div>

</body>
</html>
```